Upscale business cards needed for Board of Directors

We need professional business cards created for members of our family business Board of Directors. We would like these relatively simple and straightforward, but also with a unique element to set them apart. Probably stick with neutral and simple colors - white, grey etc. We need space for the traditional elements, including name, title, address, email/phone number. And we will be creating several from this template so it needs to be template that is easy to switch information in and out of.
Business
See description

```html
<!DOCTYPE html>
<html lang="en">
<head>
<meta charset="utf-8">
<title>Meridian Holdings – Business Card</title>
<link rel="stylesheet" href="https://fonts.googleapis.com/css2?family=Open+Sans:wght@400;600;700&display=swap">
<style>
  :root {
    --backdrop: #e6e6e4;
    --card: #ffffff;
    --ink: #231f20;
    --gold: #b09a6c;
    --muted: #7a7a7a;
  }
  * { margin: 0; padding: 0; box-sizing: border-box; }
  html, body { width: 1200px; height: 1000px; overflow: hidden; }
  body {
    position: relative;
    background: var(--backdrop);
    font-family: "Open Sans", Arial, sans-serif;
  }
  .card {
    position: absolute;
    left: 287px;
    width: 626px;
    height: 358px;
    background: var(--card);
    overflow: hidden;
  }
  .card--front { top: 140px; }
  .card--back { top: 531px; }

  .wordmark {
    position: absolute;
    color: var(--ink);
    font-weight: 700;
    text-align: center;
    line-height: 1;
  }
  .wordmark__main { display: block; font-size: 50px; letter-spacing: 0.5px; }
  .wordmark__sub { display: block; font-size: 24px; letter-spacing: 8px; margin-top: 10px; padding-left: 8px; }
  .card--front .wordmark { left: 0; right: 0; top: 146px; }

  .front__web {
    position: absolute;
    left: 0; right: 0; top: 308px;
    text-align: center;
    font-size: 14px;
    color: var(--muted);
  }

  .card--back .wordmark { right: 40px; top: 54px; width: 240px; }
  .card--back .wordmark__main { font-size: 38px; }
  .card--back .wordmark__sub { font-size: 19px; letter-spacing: 6px; margin-top: 7px; padding-left: 6px; }

  .accent-tabs { position: absolute; left: 0; top: 56px; }

  .holder { position: absolute; left: 35px; top: 52px; }
  .holder__name { font-size: 19px; font-weight: 700; color: var(--gold); line-height: 1.2; }
  .holder__title { font-size: 13.5px; color: var(--muted); line-height: 1.3; }

  .contact-list {
    position: absolute;
    left: 35px; top: 251px;
    list-style: none;
    font-size: 13.5px;
    color: var(--muted);
    line-height: 18px;
  }
  .contact-list li { display: flex; align-items: center; gap: 7px; }
  .contact-list svg { width: 11px; height: 11px; flex: none; }

  .address {
    position: absolute;
    right: 34px; top: 251px;
    text-align: right;
    font-size: 13.5px;
    color: var(--muted);
    line-height: 18px;
    font-style: normal;
  }
  .address__label { color: var(--gold); font-weight: 700; }

  .footer-band { position: absolute; left: 0; bottom: 0; }
</style>
</head>
<body>

  <section class="card card--front" aria-label="Card front">
    <div class="wordmark">
      <span class="wordmark__main">MERIDIAN</span>
      <span class="wordmark__sub">HOLDINGS</span>
    </div>
    <p class="front__web">www.meridianholdings.com</p>
  </section>

  <section class="card card--back" aria-label="Card back">
    <svg class="accent-tabs" width="26" height="32" viewBox="0 0 26 32" aria-hidden="true">
      <polygon points="0,0 11,0 7,32 0,32" fill="var(--ink)"/>
      <polygon points="14,0 25,0 21,32 10,32" fill="var(--gold)"/>
    </svg>

    <div class="holder">
      <p class="holder__name">Daniel Reyes</p>
      <p class="holder__title">President</p>
    </div>

    <div class="wordmark">
      <span class="wordmark__main">MERIDIAN</span>
      <span class="wordmark__sub">HOLDINGS</span>
    </div>

    <ul class="contact-list">
      <li>
        <svg viewBox="0 0 12 12" aria-hidden="true"><rect x="3" y="0.5" width="6" height="11" rx="1" fill="none" stroke="var(--gold)" stroke-width="1.2"/><circle cx="6" cy="9.5" r="0.7" fill="var(--gold)"/></svg>
        <span>014-555-0182</span>
      </li>
      <li>
        <svg viewBox="0 0 12 12" aria-hidden="true"><rect x="0.5" y="2.5" width="11" height="7" fill="var(--gold)"/><polyline points="0.5,2.5 6,6.5 11.5,2.5" fill="none" stroke="#fff" stroke-width="1"/></svg>
        <span>info@meridianholdings.com</span>
      </li>
      <li>
        <svg viewBox="0 0 12 12" aria-hidden="true"><circle cx="6" cy="6" r="5" fill="none" stroke="var(--gold)" stroke-width="1.1"/><ellipse cx="6" cy="6" rx="2.2" ry="5" fill="none" stroke="var(--gold)" stroke-width="0.9"/><line x1="1" y1="6" x2="11" y2="6" stroke="var(--gold)" stroke-width="0.9"/></svg>
        <span>www.meridianholdings.com</span>
      </li>
    </ul>

    <address class="address">
      <span class="address__label">Address</span><br>
      Street name, Suite 100 State,<br>
      Zip Code, Country
    </address>

    <svg class="footer-band" width="626" height="24" viewBox="0 0 626 24" aria-hidden="true">
      <polygon points="0,11 302,11 290,24 0,24" fill="var(--ink)"/>
      <polygon points="314,0 626,0 626,24 291,24" fill="var(--gold)"/>
    </svg>
  </section>

</body>
</html>
```